Business card for Eyelash extension salon in Rosemere Hills,California USA

We need new business card for our salon in Rosemere Hills. The salon name is 'Lashvera' . We would like to have...Business name: Lashvera Name of person: will provide later Address 4720 N.Alder Crest Ave Rosemere Hills , CA 91877 Phone: will provide later (Text only) Web: www.lashverastudio.example Snapgrid icon, Circlebook icon follow us for seasonal campaign and news @lashverastudiolounge Design should look elegant, high-end, clean, simple, cohesive with my brand. Please refer my brand board. Business name color will be metallic bronzy color. Im thinking grey background or white background. Thanks

Target Market(s)

25-35. Gender neutral. People who are in Entertainment business industry.
This is High-end Eyelash extension salon in Rosemere Hills

Industry/Entity Type

Beauty Salon

Contact Information for Business Card

Business name: Lashvera
Name of person: will provide later
Address 4720 N.Alder Crest Ave Rosemere Hills , CA 91877
Phone: will provide later (Text only)
Web: www.lashverastudio.example
Snapgrid icon, Circlebook icon
follow us for seasonal campaign and news @lashverastudiolounge

Requirements
Must have
• Beautiful, elegant, clean and simple look but very attractive and modern
Should not have
• We don't like too clutter, too busy designs.

```html
<!DOCTYPE html>
<html lang="en">
<head>
<meta charset="utf-8">
<title>Lashvera – Business Card</title>
<link href="https://fonts.googleapis.com/css2?family=Crimson+Text:wght@400;600&family=DM+Serif+Display&family=Josefin+Sans:wght@400&display=swap" rel="stylesheet">
<style>
  :root {
    --backdrop: #1d1d1d;
    --card: #ffffff;
    --gold: #c9922b;
    --bronze: #7b5a48;
    --marble-light: #f1f1f1;
    --marble-mid: #d6d6d6;
  }
  html, body {
    margin: 0;
    width: 1200px;
    height: 741px;
    overflow: hidden;
    background: var(--backdrop);
  }
  .stage {
    position: relative;
    width: 1200px;
    height: 741px;
  }
  .card {
    position: absolute;
    width: 302px;
    height: 302px;
    border-radius: 22px;
    overflow: hidden;
    background: var(--card);
  }
  .card--front { left: 273px; top: 190px; }
  .card--back  { left: 622px; top: 189px; width: 305px; height: 305px; }
  .card__art {
    position: absolute;
    inset: 0;
    width: 100%;
    height: 100%;
  }
  .brand {
    position: absolute;
    left: 0;
    right: 0;
    top: 118px;
    text-align: center;
    color: var(--gold);
  }
  .brand__name {
    font-family: "Crimson Text", serif;
    font-weight: 400;
    font-size: 46px;
    line-height: 1;
    letter-spacing: 1px;
  }
  .brand__place {
    margin-top: 8px;
    margin-left: 70px;
    font-family: "Josefin Sans", sans-serif;
    font-size: 7px;
    letter-spacing: 1.6px;
  }
  .contact {
    position: absolute;
    left: 0;
    right: 0;
    top: 60px;
    text-align: center;
    color: var(--bronze);
    font-family: "Crimson Text", serif;
    font-size: 13px;
    line-height: 15px;
  }
  .contact__name {
    font-family: "DM Serif Display", serif;
    font-size: 26px;
    line-height: 26px;
  }
  .contact__role { margin-bottom: 20px; }
  .contact__label { font-weight: 600; }
  .contact__web {
    margin-top: 14px;
    letter-spacing: 1px;
    font-weight: 600;
  }
  .contact__social {
    margin-top: 10px;
    font-size: 13px;
  }
  .contact__dot {
    display: inline-block;
    width: 8px;
    height: 8px;
    border: 1px solid var(--bronze);
    vertical-align: -1px;
    margin-right: 4px;
  }
</style>
</head>
<body>
<main class="stage">

  <section class="card card--front">
    <svg class="card__art" viewBox="0 0 302 302">
      <defs>
        <linearGradient id="marble" x1="0" y1="0" x2="1" y2="1">
          <stop offset="0" stop-color="var(--marble-light)"/>
          <stop offset="0.5" stop-color="var(--marble-mid)"/>
          <stop offset="1" stop-color="var(--marble-light)"/>
        </linearGradient>
      </defs>
      <g role="img" aria-label="White and grey marble texture bands">
        <polygon points="0,88 88,0 156,0 0,156" fill="url(#marble)"/>
        <polygon points="214,0 302,88 302,156 146,0" fill="url(#marble)"/>
        <polygon points="0,214 88,302 156,302 0,146" fill="url(#marble)"/>
        <polygon points="302,214 214,302 146,302 302,146" fill="url(#marble)"/>
      </g>
      <polygon points="151,6 296,151 151,296 6,151" fill="var(--card)" stroke="var(--gold)" stroke-width="0.8"/>
      <g stroke="var(--gold)" stroke-width="1.6">
        <line x1="0" y1="88" x2="88" y2="0"/>
        <line x1="214" y1="0" x2="302" y2="88"/>
        <line x1="0" y1="214" x2="88" y2="302"/>
        <line x1="302" y1="214" x2="214" y2="302"/>
      </g>
    </svg>
    <div class="brand">
      <div class="brand__name">Lashvera</div>
      <div class="brand__place">ROSEMERE HILLS</div>
    </div>
  </section>

  <section class="card card--back">
    <svg class="card__art" viewBox="0 0 305 305">
      <defs>
        <linearGradient id="marble-back" x1="0" y1="0" x2="1" y2="1">
          <stop offset="0" stop-color="var(--marble-mid)"/>
          <stop offset="1" stop-color="var(--marble-light)"/>
        </linearGradient>
      </defs>
      <g role="img" aria-label="White and grey marble texture corners">
        <polygon points="0,0 103,0 0,103" fill="url(#marble-back)"/>
        <polygon points="305,0 202,0 305,103" fill="url(#marble-back)"/>
        <polygon points="0,305 103,305 0,202" fill="url(#marble-back)"/>
        <polygon points="305,305 202,305 305,202" fill="url(#marble-back)"/>
      </g>
      <g stroke="var(--gold)" stroke-width="1.2">
        <line x1="0" y1="103" x2="103" y2="0"/>
        <line x1="202" y1="0" x2="305" y2="103"/>
        <line x1="0" y1="202" x2="103" y2="305"/>
        <line x1="305" y1="202" x2="202" y2="305"/>
      </g>
    </svg>
    <div class="contact">
      <div class="contact__name">Dario Wren</div>
      <div class="contact__role">Owner</div>
      <div><span class="contact__label">P:</span> +1 555 014 2290</div>
      <div><span class="contact__label">E:</span> info@lashverastudio.example</div>
      <div>4720 N.Alder Crest Ave Rosemere Hills</div>
      <div>CA 91877</div>
      <div class="contact__web">www.lashverastudio.example</div>
      <div class="contact__social"><span class="contact__dot"></span>Circlebook · Snapgrid</div>
      <div>@lashverastudiolounge</div>
    </div>
  </section>

</main>
</body>
</html>
```